New Business Card for Web Design/Internet Marketing Company

Looking for a great looking new business card. We are a 10 year old web design, internet marketing and website management company that works mostly with small businesses.

Our new card needs to better match the colors and style of our website, be bold, extremely usable and slightly edgy.

Target Market(s)

Small/Medium businesses that have websites

Industry/Entity Type

Internet

Requirements
Must have
• Front and back design, full color, rounded corners please

Must use the colors/style of our website (JPG provided)

INFO FOR CARDS (as readable as possible please)
Mark Lenner
President/CEO
mark@trelvanmedia.example
Phone: 520-381-7459
Toll Free: 866-381-7459
Address: 4315 W. Calloway Ave. Ste. 140, Tucson, AZ 85792

THINGS I WANT TO PROMOTE (if there is room):
1. Our Website - www.trelvanmedia.example

2. Social Media
Twitter: @trelvanmedia
Facebook: www.facebook.com/trelvanmedia

3. Our Services
Web Design
Internet Marketing
Website Management

```html
<!DOCTYPE html>
<html lang="en">
<head>
<meta charset="utf-8">
<title>Trelvan Media – Business Card</title>
<link rel="stylesheet" href="https://fonts.googleapis.com/css2?family=Open+Sans:wght@400;600;700;800&display=swap">
<style>
  :root {
    --brand-blue: #1b8fca;
    --brand-orange: #f0892f;
    --ink: #4a4a4a;
    --paper: #ffffff;
    --backdrop: #eceae6;
  }
  * { box-sizing: border-box; margin: 0; padding: 0; }
  html, body { width: 1200px; height: 402px; overflow: hidden; }
  body {
    background: var(--backdrop);
    font-family: "Open Sans", Arial, sans-serif;
    position: relative;
  }
  .card {
    position: absolute;
    top: 56px;
    width: 512px;
    height: 290px;
    border-radius: 18px;
    overflow: hidden;
    box-shadow: 0 4px 14px rgba(0,0,0,.18);
  }
  .card--front { left: 63px; background: var(--paper); }
  .card--back { left: 626px; background: var(--brand-blue); color: #fff; }

  .front-band { position: absolute; left: 0; top: 0; width: 512px; height: 290px; }

  .brand {
    position: absolute;
    left: 52px;
    top: 58px;
    display: flex;
    align-items: center;
    gap: 12px;
  }
  .brand__dot {
    width: 38px; height: 38px; border-radius: 50%;
    background: var(--brand-orange);
  }
  .brand__name {
    font-weight: 800;
    font-size: 40px;
    letter-spacing: -1px;
    color: var(--brand-blue);
    line-height: 1;
  }
  .tagline {
    position: absolute;
    right: 48px;
    top: 108px;
    font-size: 15px;
    color: var(--ink);
  }

  .contact {
    position: absolute;
    right: 212px;
    top: 190px;
    text-align: right;
    font-size: 11.5px;
    line-height: 16.5px;
    color: #fff;
  }
  .contact__row { display: flex; justify-content: flex-end; align-items: center; gap: 5px; }
  .contact__icon { width: 9px; height: 9px; border-radius: 50%; background: #fff; flex: none; }
  .contact__icon--square { border-radius: 2px; }
  .contact__address { margin-top: 1px; line-height: 14px; }

  .divider {
    position: absolute;
    left: 320px; top: 190px;
    width: 1px; height: 92px;
    background: rgba(255,255,255,.8);
  }
  .person {
    position: absolute;
    left: 330px; width: 120px;
    top: 222px;
    text-align: center;
    color: #fff;
  }
  .person__name { font-size: 15px; font-weight: 700; }
  .person__title { font-size: 11.5px; }

  .back-brand {
    position: absolute;
    left: 32px; top: 152px;
    display: flex; align-items: center; gap: 12px;
  }
  .back-brand__dot { width: 40px; height: 40px; border-radius: 50%; background: #fff; }
  .back-brand__name { font-size: 46px; font-weight: 800; letter-spacing: -1px; line-height: 1; color: #fff; }

  .social {
    position: absolute;
    left: 274px; top: 42px;
    font-size: 15px;
    line-height: 24px;
  }
  .social__row { display: flex; align-items: center; gap: 10px; }
  .social__mark { width: 16px; height: 16px; border-radius: 3px; background: rgba(255,255,255,.55); }

  .services {
    position: absolute;
    left: 274px; top: 164px;
    font-size: 21px;
    line-height: 31px;
  }
</style>
</head>
<body>

  <section class="card card--front" aria-label="Business card front">
    <svg class="front-band" viewBox="0 0 512 290" aria-hidden="true">
      <path d="M0 148 Q256 168 512 140 L512 290 L0 290 Z" fill="var(--brand-blue)"/>
      <path d="M0 144 Q256 164 512 136 L512 146 Q256 174 0 154 Z" fill="var(--brand-orange)"/>
      <path d="M382 152 L410 150 L396 170 Z" fill="var(--brand-orange)"/>
      <path d="M387 155 L405 154 L396 165 Z" fill="var(--brand-blue)"/>
    </svg>

    <div class="brand">
      <span class="brand__dot"></span>
      <span class="brand__name">trelvanmedia</span>
    </div>
    <p class="tagline">Built to grow online</p>

    <div class="contact">
      <div class="contact__row">520-381-7459 <span class="contact__icon"></span></div>
      <div class="contact__row">866-381-7459 <span class="contact__icon"></span></div>
      <div class="contact__row">mark@trelvanmedia.example <span class="contact__icon contact__icon--square"></span></div>
      <div class="contact__row">www.trelvanmedia.example <span class="contact__icon"></span></div>
      <div class="contact__address">4315 W. Calloway Ave., Ste. 140<br>Tucson, AZ 85792</div>
    </div>
    <div class="divider"></div>
    <div class="person">
      <p class="person__name">Mark Lenner</p>
      <p class="person__title">President/CEO</p>
    </div>
  </section>

  <section class="card card--back" aria-label="Business card back">
    <div class="social">
      <div class="social__row"><span class="social__mark"></span>@trelvanmedia</div>
      <div class="social__row"><span class="social__mark"></span>trelvanmedia</div>
    </div>
    <div class="back-brand">
      <span class="back-brand__dot"></span>
      <span class="back-brand__name">trelvan</span>
    </div>
    <div class="services">
      <p>Web Design</p>
      <p>Internet Marketing</p>
      <p>Website Management</p>
    </div>
  </section>

</body>
</html>
```